Heron Loan Partners Business Card

We need a business card design for our mortgage servicing company. In addition to servicing the loans of homeowners, we help homeowners with purchasing their homes and any mortgage refinancing. We would like to see designs that use the colors in the logo attached below (gold-ish yellow and navy blue), and any other design you deem fit! The design should communicate a simpler life with smart mortgages provided by Heron.

```html
<!DOCTYPE html>
<html lang="en">
<head>
<meta charset="utf-8">
<title>Heron Loan Partners Business Card</title>
<link href="https://fonts.googleapis.com/css2?family=Open+Sans:wght@400;600;700&display=swap" rel="stylesheet">
<style>
  :root {
    --canvas-bg: #e9e6e1;
    --card-dark: #1e1f24;
    --card-gold: #dfb43f;
    --navy: #1f1f5c;
    --gold: #dfb43f;
    --text-light: #f2f2f2;
    --emboss: #2a2b31;
  }
  * { box-sizing: border-box; margin: 0; padding: 0; }
  html, body { width: 1200px; height: 780px; overflow: hidden; }
  body {
    background: var(--canvas-bg);
    font-family: "Open Sans", Arial, sans-serif;
    display: flex;
    align-items: center;
    justify-content: center;
    gap: 40px;
  }
  .card {
    position: relative;
    width: 540px;
    height: 309px;
    box-shadow: 0 10px 24px rgba(0,0,0,0.22);
    overflow: hidden;
  }
  /* Back side */
  .card--back { background: var(--card-dark); color: var(--text-light); }
  .brand-name {
    font-family: "Open Sans", Arial, sans-serif;
    font-weight: 700;
    white-space: nowrap;
  }
  .card--back .brand-name {
    position: absolute;
    left: 52px; top: 34px;
    font-size: 22px;
    color: var(--gold);
  }
  .contact {
    position: absolute;
    left: 40px; top: 100px;
    list-style: none;
    font-size: 12.5px;
    line-height: 19px;
  }
  .contact li { display: flex; align-items: center; gap: 7px; }
  .contact .address { padding-left: 21px; }
  .contact svg { width: 14px; height: 14px; flex: none; }
  .person {
    position: absolute;
    right: 44px; top: 138px;
    text-align: right;
  }
  .person__name { font-size: 24px; font-weight: 700; letter-spacing: 0.5px; }
  .person__first { color: var(--gold); }
  .person__role { font-size: 13px; margin-top: 2px; }
  .edge-tab {
    position: absolute;
    right: 0; top: 150px;
    width: 22px; height: 40px;
    background: var(--gold);
  }
  .card--back .brand-name--faint {
    left: 150px; top: 220px;
    font-size: 34px;
    color: var(--emboss);
  }
  /* Front side */
  .card--front {
    background: var(--card-gold);
    display: flex;
    align-items: center;
    justify-content: center;
  }
  .card--front .brand-name {
    font-size: 36px;
    color: var(--navy);
  }
</style>
</head>
<body>
  <section class="card card--back" aria-label="Business card, back">
    <div class="brand-name">Heron Loan Partners</div>
    <ul class="contact">
      <li class="address">1840 Lakeside Ave. Suite 310</li>
      <li class="address">Riverton, TX 75010</li>
      <li>
        <svg viewBox="0 0 14 14" aria-hidden="true"><circle cx="7" cy="7" r="7" fill="#dfb43f"/><path d="M4.3 3.6l1.5-.3.8 1.9-.9.7a5 5 0 0 0 2.4 2.4l.7-.9 1.9.8-.3 1.5c-3.3.1-6.2-2.8-6.1-6.1z" fill="#1e1f24"/></svg>
        (555) 214-6083
      </li>
      <li>
        <svg viewBox="0 0 14 14" aria-hidden="true"><circle cx="7" cy="7" r="7" fill="#dfb43f"/><rect x="3.5" y="4.5" width="7" height="5" fill="none" stroke="#1e1f24" stroke-width="1"/><path d="M3.5 4.5L7 7.5l3.5-3" fill="none" stroke="#1e1f24" stroke-width="1"/></svg>
        info@heronloan.com
      </li>
      <li>
        <svg viewBox="0 0 14 14" aria-hidden="true"><circle cx="7" cy="7" r="7" fill="#dfb43f"/><circle cx="7" cy="7" r="3.6" fill="none" stroke="#1e1f24" stroke-width="1"/><path d="M3.4 7h7.2M7 3.4c-1.6 2-1.6 5.2 0 7.2M7 3.4c1.6 2 1.6 5.2 0 7.2" fill="none" stroke="#1e1f24" stroke-width="0.8"/></svg>
        www.heronloan.com
      </li>
    </ul>
    <div class="person">
      <div class="person__name"><span class="person__first">Dana</span> Velkova</div>
      <div class="person__role">Managing Director</div>
    </div>
    <div class="edge-tab"></div>
    <div class="brand-name brand-name--faint" aria-hidden="true">Heron Loan Partners</div>
  </section>

  <section class="card card--front" aria-label="Business card, front">
    <div class="brand-name">Heron Loan Partners</div>
  </section>
</body>
</html>
```